Stylish Business Cards Wanted

- DOUBLE SIDED Design Required -

High end, edgy cards for a corporate and personal stylist. Must include logo,
Name: Belinda Harwick
Title: Director and Stylist
telephone : +61 8 7142 5809
email: belinda@theloombriefing.example
website: theloombriefing.example
Tag: Corporate Workwear & Uniform Specialist | Personal Stylist
Would like nice icons for telephone, email, website

Target Market(s)

Businesses wanting stylish uniforms, people wanting stylish wardrobes

Industry/Entity Type

Corporate Workwear Stylist

Contact Information for Business Card

I would like black, white and gold foiling incorporated in the design - possibly a touch of the other colours on my branding guide attached Name: Belinda Harwick Title: Director and Stylist telephone : +61 8 7142 5809 email: belinda@theloombriefing.example website: theloombriefing.example Tag: Corporate Workwear & Uniform Specialist | Personal Stylist Would like nice icons for telephone, email, website

Font styles to use
Other font styles liked:
• Raleway

Colors

Designer to choose colors to be used in the design.

Requirements
Must have
• Gold foil accents

```html
<!DOCTYPE html>
<html lang="en">
<head>
<meta charset="utf-8">
<title>The Loom Briefing – Business Cards</title>
<link href="https://fonts.googleapis.com/css2?family=Roboto:wght@400;500;700&display=swap" rel="stylesheet">
<style>
  :root {
    --stage: #1c1c1c;
    --card-black: #232323;
    --card-white: #ffffff;
    --gold: #e5bd5a;
    --ink: #1f1f1f;
    --light-text: #ffffff;
  }
  * { margin: 0; padding: 0; box-sizing: border-box; }
  html, body { width: 1200px; height: 988px; overflow: hidden; }
  body {
    background: var(--stage);
    font-family: "Roboto", Arial, sans-serif;
    position: relative;
  }
  .card {
    position: absolute;
    width: 520px;
    height: 297px;
    border-radius: 16px;
    overflow: hidden;
  }
  .card-front {
    left: 90px;
    top: 120px;
    background: var(--card-black);
  }
  .card-back {
    left: 590px;
    top: 560px;
    background: var(--card-white);
  }
  .brand-name {
    position: absolute;
    font-family: "Roboto", Arial, sans-serif;
    font-weight: 500;
    letter-spacing: 0.5px;
    line-height: 1;
    white-space: nowrap;
  }
  .card-front .brand-name {
    color: var(--light-text);
    font-size: 34px;
    left: 0; right: 0;
    top: 100px;
    text-align: center;
  }
  .tagline {
    position: absolute;
    left: 0; right: 0;
    top: 232px;
    text-align: center;
    color: var(--gold);
    font-size: 13.5px;
    letter-spacing: 0.2px;
  }
  .card-back .brand-name {
    color: var(--ink);
    font-size: 28px;
    left: 40px;
    top: 64px;
  }
  .wave {
    position: absolute;
    inset: 0;
    width: 520px;
    height: 297px;
  }
  .contact {
    position: absolute;
    right: 26px;
    top: 108px;
    text-align: right;
    color: var(--light-text);
  }
  .contact-name {
    color: var(--gold);
    font-weight: 700;
    font-size: 17px;
    letter-spacing: 0.3px;
    text-transform: uppercase;
  }
  .contact-title {
    font-size: 12.5px;
    margin-top: 2px;
    margin-bottom: 14px;
  }
  .contact-line {
    display: flex;
    justify-content: flex-end;
    align-items: center;
    gap: 7px;
    font-size: 12.5px;
    margin-top: 5px;
  }
  .contact-icon {
    width: 14px;
    height: 14px;
    flex: none;
  }
</style>
</head>
<body>

  <section class="card card-front" aria-label="Business card front">
    <div class="brand-name">The Loom Briefing</div>
    <p class="tagline">Corporate Workwear &amp; Uniform Specialist | Personal Stylist</p>
  </section>

  <section class="card card-back" aria-label="Business card back">
    <svg class="wave" viewBox="0 0 520 297" aria-hidden="true">
      <path d="M0,297 L0,262 C110,262 190,252 265,188 C335,128 400,82 520,62 L520,297 Z" fill="var(--card-black)"/>
      <path d="M0,243 C110,268 200,240 270,168 C340,98 400,68 470,58" fill="none" stroke="var(--gold)" stroke-width="8" stroke-linecap="round"/>
      <path d="M130,262 C210,258 250,228 300,178 C360,118 410,84 480,68" fill="none" stroke="var(--card-black)" stroke-width="5" stroke-linecap="round"/>
    </svg>

    <div class="brand-name">The Loom Briefing</div>

    <div class="contact">
      <div class="contact-name">Belinda Harwick</div>
      <div class="contact-title">Director and Stylist</div>
      <div class="contact-line">
        <span>+61 8 7142 5809</span>
        <svg class="contact-icon" viewBox="0 0 14 14" aria-hidden="true">
          <circle cx="7" cy="7" r="7" fill="var(--gold)"/>
          <path d="M4.3,3.6 l1.4,-0.3 l0.8,1.8 l-0.9,0.7 c0.4,1 1.1,1.7 2.1,2.1 l0.7,-0.9 l1.8,0.8 l-0.3,1.4 c-3,0.2 -5.8,-2.6 -5.6,-5.6 z" fill="var(--card-black)"/>
        </svg>
      </div>
      <div class="contact-line">
        <span>belinda@theloombriefing.example</span>
        <svg class="contact-icon" viewBox="0 0 14 14" aria-hidden="true">
          <circle cx="7" cy="7" r="7" fill="var(--gold)"/>
          <rect x="3.2" y="4.3" width="7.6" height="5.4" fill="var(--card-black)"/>
          <path d="M3.4,4.5 L7,7.4 L10.6,4.5" fill="none" stroke="var(--gold)" stroke-width="0.8"/>
        </svg>
      </div>
      <div class="contact-line">
        <span>www.theloombriefing.example</span>
        <svg class="contact-icon" viewBox="0 0 14 14" aria-hidden="true">
          <circle cx="7" cy="7" r="7" fill="var(--gold)"/>
          <circle cx="7" cy="7" r="3.8" fill="none" stroke="var(--card-black)" stroke-width="0.9"/>
          <ellipse cx="7" cy="7" rx="1.6" ry="3.8" fill="none" stroke="var(--card-black)" stroke-width="0.8"/>
          <line x1="3.2" y1="7" x2="10.8" y2="7" stroke="var(--card-black)" stroke-width="0.8"/>
        </svg>
      </div>
    </div>
  </section>

</body>
</html>
```